Brightline Energy Product Distribution Brochure

We are looking to have our current brochure for our customers completely redesigned...the idea is to present the relevant information in an attractive way . Our website is brightlineenergyco.example where you can find more information about us. We have included a file with a rough idea of the page order and what each should include but feel free to adapt based on design. The example provided is only for context and doesnt have to be maintained. We will be using the brochure both digitally and in print form. As long as it reads easily and is eye catching, the design can be horizontal or vertical.Final deliverable should be indesign file.

"Our Brands" page: should be limited to one page (space being enough) where it has the header for each one (for example diesel generators) space for one or two lines of text and then the corresponding logos for each of the five categories
Updates

For those asking: the "our brands" page should be a single page layout where there is a header with the corresponding section and space for maybe one line of text followed by the two logos for that category. Each of the product pages should be similar in fashion to the one in the document attached: a photo of the product with some white space and space for the text to be included. We will be posting additional examples today

Target Market(s)

We want to present it to customers both digitally and in print so they can see our products

Industry/Entity Type

Power Generation

Font styles to use
Serif

Requirements
Must have
• Eye catching and able to present the information in a presentable fashion. Rest is up to you.
Nice to have
• Should incorporate the colors of our logo but can also add other depending on design

```html
<!DOCTYPE html>
<html lang="en">
<head>
<meta charset="utf-8">
<title>Brightline Energy – Brochure Spread</title>
<link href="https://fonts.googleapis.com/css2?family=Montserrat:wght@300;400;500&display=swap" rel="stylesheet">
<style>
  :root{
    --backdrop:#e4e2dc;
    --paper:#ffffff;
    --accent:#e8a630;
    --ink-grey:#7d7b78;
    --ink-dark:#3c3a37;
    --photo-dark:#2f2a20;
    --photo-mid:#8a6a10;
    --photo-yellow:#e8b800;
    --panel:rgba(58,40,14,0.74);
    --panel-text:#f3ead6;
  }
  *{box-sizing:border-box;margin:0;padding:0}
  html,body{width:1200px;height:960px;overflow:hidden}
  body{background:var(--backdrop);font-family:"Montserrat",sans-serif;position:relative}
  .spread{position:absolute;left:60px;top:160px;width:1080px;height:640px;box-shadow:0 18px 40px rgba(0,0,0,.18)}
  .spread svg{position:absolute;inset:0}
  .index{position:absolute;left:44px;top:58px;width:260px;color:var(--ink-grey);font-weight:300;font-size:10.5px;letter-spacing:.04em;text-transform:uppercase}
  .index-title{color:var(--accent);font-weight:300;font-size:26px;letter-spacing:.03em;margin-bottom:10px}
  .index ul{list-style:none}
  .index li{position:relative;line-height:13.4px}
  .index .section{color:var(--ink-dark);font-weight:400}
  .index .l1{padding-left:36px}
  .index .l2{padding-left:74px}
  .index .page{position:absolute;left:240px;top:0;white-space:nowrap;font-size:9.5px}
  .about{position:absolute;left:570px;top:100px;width:440px;color:var(--panel-text)}
  .about h2{font-weight:300;font-size:24px;letter-spacing:.05em;color:#fff;margin-bottom:12px}
  .about .cols{display:flex;gap:18px}
  .about .col{flex:1;font-size:9px;line-height:12.5px;font-weight:300}
  .about p{margin-bottom:7px}
</style>
</head>
<body>
<main class="spread">
  <svg viewBox="0 0 1080 640" width="1080" height="640">
    <defs>
      <linearGradient id="engine" x1="0" y1="0" x2="1" y2="1">
        <stop offset="0" stop-color="var(--photo-dark)"/>
        <stop offset=".35" stop-color="var(--photo-mid)"/>
        <stop offset=".7" stop-color="var(--photo-yellow)"/>
        <stop offset="1" stop-color="#c99a08"/>
      </linearGradient>
    </defs>
    <rect class="page-left" x="0" y="0" width="540" height="640" fill="var(--paper)"/>
    <g role="img" aria-label="Photograph of a large yellow diesel generator engine">
      <polygon points="290,0 1080,0 1080,640 540,640" fill="url(#engine)"/>
    </g>
    <polygon class="corner-fold" points="955,0 1080,0 1080,240" fill="var(--paper)"/>
    <rect class="about-panel" x="555" y="70" width="495" height="500" fill="var(--panel)"/>
    <line x1="540" y1="0" x2="540" y2="640" stroke="rgba(0,0,0,.12)" stroke-width="1"/>
  </svg>

  <section class="index">
    <h1 class="index-title">INDEX</h1>
    <ul>
      <li class="section">"About our company"<span class="page">(Page 3)</span></li>
      <li class="section">"Our brands"<span class="page">(Page 4)</span></li>
      <li class="l1">Diesel generators</li>
      <li class="l2">Brightline Energy</li>
      <li class="l2">Halvorsen-DMX</li>
      <li class="l1">AC alternators</li>
      <li class="l2">Stanbridge-AVT</li>
      <li class="l2">Larue Mercer</li>
      <li class="l1">Alternator parts</li>
      <li class="l2">Stanbridge-AVT</li>
      <li class="l2">Larue Mercer</li>
      <li class="l1">Controls</li>
      <li class="l2">Coral Bay Controls</li>
      <li class="l2">DMX</li>
      <li class="l1">Transfer switches</li>
      <li class="l2">Aldena</li>
      <li class="l2">Thornbury</li>
      <li class="section">"Our stock"</li>
      <li class="section">"Our products"<span class="page">(Page 5)</span></li>
      <li class="l1">Diesel generators</li>
      <li class="l2">Standby generators<span class="page">(Page 6)</span></li>
      <li class="l2">Prime generators<span class="page">(Page 7)</span></li>
      <li class="l2">Rental generators<span class="page">(Page 8)</span></li>
      <li class="l1">AC alternators<span class="page">(Page 9)</span></li>
      <li class="l1">Alternator parts<span class="page">(Page 10)</span></li>
      <li class="l1">Controllers<span class="page">(Page 11)</span></li>
      <li class="l1">Transfer switches<span class="page">(Page 12)</span></li>
      <li class="section">"Our distributors"<span class="page">(Page 13)</span></li>
    </ul>
  </section>

  <section class="about">
    <h2>ABOUT OUR COMPANY</h2>
    <div class="cols">
      <div class="col">
        <p>Brightline Energy has supplied dependable power equipment to industrial, commercial and residential customers for more than two decades, building lasting relationships through honest advice and responsive service.</p>
        <p>Our team helps every client choose the right generator, alternator or controller for the job, from small standby units to large prime power installations.</p>
        <p>We keep a deep inventory ready to ship, so projects stay on schedule and downtime stays short.</p>
      </div>
      <div class="col">
        <p>Every unit we sell is backed by trusted manufacturers, tested components and technicians who know the equipment inside and out.</p>
        <p>Whether you need a rental generator for an event or a permanent system for a hospital, our specialists guide you from quote to commissioning.</p>
        <p>Through a growing network of distributors, we deliver power solutions across the country and beyond, with parts support long after installation.</p>
      </div>
    </div>
  </section>
</main>
</body>
</html>
```